Cognitive therapist.

I am a therapist and my main work is with clients who have depression and anxiety disorders.

I need something reasonably plain. Cognitive therapy is a very pragmatic approach to dealing with problems, so it isn't new agey (no offence to new age therapies at all)
Updates

Hi everyone, I am currently looking at a particular design that I will most likely go with. Cheers, Meg

Industry/Entity Type

Work

Contact Information for Business Card

Meg Tarvish
Cognitive Therapist
BA, PG Dip Mental Health,
PG Dip Cog Beh Therapy
MKTPR

The Quarry Lodge,
Level One
48 Marlow Parade
Cnr Fenwick St & Marlow Parade
P O Box 38 219
WELLINGTON 6143

Phone: 021 574 3082 Email: mtarvish@quellnet.co.nz

www.megtarvish.co.nz

Requirements
Should not have
• No illustration, or colour. not old style fonts.

```html
<!DOCTYPE html>
<html lang="en">
<head>
<meta charset="utf-8">
<title>Meg Tarvish – Business Card</title>
<link rel="stylesheet" href="https://fonts.googleapis.com/css2?family=Source+Sans+3:ital,wght@0,400;0,600;0,700;1,400;1,600;1,700&display=swap">
<style>
  :root {
    --backdrop: #8a5c3b;
    --teal-dark: #0b5866;
    --teal-deep: #073f4a;
    --cyan: #1fb3d6;
    --silver-light: #f4f6f7;
    --silver-mid: #b9c0c4;
    --silver-dark: #7d878c;
    --ink: #10243a;
    --white: #ffffff;
    --photo-light: #9b9b9b;
    --photo-dark: #3c3c3c;
  }
  * { margin: 0; padding: 0; box-sizing: border-box; }
  html, body {
    width: 1200px;
    height: 864px;
    overflow: hidden;
    background: var(--backdrop);
    font-family: "Source Sans 3", sans-serif;
  }
  .business-card {
    position: absolute;
    left: 178px;
    top: 188px;
    width: 843px;
    height: 488px;
    background: var(--cyan);
    overflow: hidden;
  }
  .card-shapes {
    position: absolute;
    inset: 0;
    width: 843px;
    height: 488px;
  }
  .portrait {
    position: absolute;
    left: 0;
    top: 31px;
    width: 280px;
    height: 457px;
    background: linear-gradient(160deg, var(--photo-light) 0%, #6e6e6e 55%, var(--photo-dark) 100%);
  }
  .identity {
    position: absolute;
    left: 282px;
    top: 48px;
    color: var(--white);
  }
  .identity .name {
    font-size: 54px;
    font-weight: 700;
    line-height: 1;
    letter-spacing: 0.2px;
  }
  .identity .role {
    margin-top: 10px;
    font-size: 18px;
    font-weight: 700;
    font-style: italic;
  }
  .identity .qualifications {
    margin-top: 36px;
    font-size: 17px;
    font-style: italic;
    line-height: 24px;
  }
  .contact {
    position: absolute;
    right: 21px;
    top: 214px;
    text-align: right;
    font-size: 19px;
    line-height: 28px;
    color: var(--white);
  }
  .contact .label {
    font-weight: 700;
    color: var(--ink);
  }
  .contact .website {
    font-weight: 700;
    color: var(--ink);
    font-size: 21px;
    letter-spacing: 1px;
    margin-top: 2px;
  }
  .address {
    position: absolute;
    left: 532px;
    top: 354px;
    font-size: 18.5px;
    line-height: 26.5px;
    color: var(--white);
  }
</style>
</head>
<body>
  <div class="business-card">
    <svg class="card-shapes" viewBox="0 0 843 488" aria-hidden="true">
      <defs>
        <linearGradient id="panelTeal" x1="0" y1="0" x2="1" y2="1">
          <stop offset="0" stop-color="var(--teal-deep)"/>
          <stop offset="0.6" stop-color="var(--teal-dark)"/>
          <stop offset="1" stop-color="var(--teal-deep)"/>
        </linearGradient>
        <linearGradient id="silverBand" x1="0" y1="0" x2="0" y2="1">
          <stop offset="0" stop-color="var(--silver-mid)"/>
          <stop offset="0.35" stop-color="var(--silver-light)"/>
          <stop offset="0.7" stop-color="var(--silver-dark)"/>
          <stop offset="1" stop-color="var(--silver-light)"/>
        </linearGradient>
      </defs>
      <path d="M0 0 H640 C628 190 560 380 372 488 H0 Z" fill="url(#silverBand)"/>
      <path d="M0 0 H618 C606 190 530 380 346 488 H0 Z" fill="url(#panelTeal)"/>
    </svg>

    <div class="portrait" role="img" aria-label="Black and white portrait photograph of the therapist"></div>

    <div class="identity">
      <h1 class="name">Meg Tarvish</h1>
      <p class="role">Cognitive Therapist BA</p>
      <p class="qualifications">PG Dip Mental Health,<br>PG Dip Cog Beh Therapy</p>
    </div>

    <div class="contact">
      <p><span class="label">Phone:</span> 021 574 3082</p>
      <p><span class="label">Email:</span> mtarvish@quellnet.co.nz</p>
      <p class="website">www.megtarvish.co.nz</p>
    </div>

    <address class="address" style="font-style: normal;">
      MKTPR The Quarry Lodge, Level<br>
      One 48 Marlow Parade Cnr Fenwick St<br>
      &amp; Marlow Parade P O Box 38 219<br>
      WELLINGTON 6143
    </address>
  </div>
</body>
</html>
```